Health Care Company with Logo Needs Business Cards designed

We are a luxury behavioral health company looking for business cards design we already have a logo and are looking for someone to design a sophisticated luxurious looking business card. Please note that Card design should be captivating just like the logo and also encompass the logo color

Industry/Entity Type

Healthcare

Contact Information for Business Card

Logo,company name, tagline, my name and title, contact details, and physical address

```html
<!DOCTYPE html>
<html lang="en">
<head>
<meta charset="utf-8">
<title>Harbor Crest Behavioral Health – Business Card</title>
<link rel="stylesheet" href="https://fonts.googleapis.com/css2?family=Roboto:wght@400;500&family=Roboto+Condensed:wght@700&display=swap">
<style>
  :root {
    --stage: #202022;
    --paper: #ffffff;
    --purple: #7a3e9d;
    --purple-deep: #5e2a7e;
    --sky: #00aeef;
    --orange: #f7941d;
    --green: #8dc63f;
    --ink: #2b2b2b;
  }
  * { box-sizing: border-box; margin: 0; padding: 0; }
  html, body { width: 1200px; height: 900px; overflow: hidden; }
  body {
    background: var(--stage);
    font-family: "Roboto", Arial, sans-serif;
    display: flex;
    flex-direction: column;
    align-items: center;
    justify-content: center;
    gap: 34px;
  }
  .card {
    width: 700px;
    height: 400px;
    position: relative;
    overflow: hidden;
  }
  /* Front */
  .card-front { background: var(--paper); color: var(--ink); }
  .brand {
    position: absolute;
    left: 48px;
    top: 44px;
  }
  .brand-row { display: flex; align-items: center; gap: 12px; }
  .brand-mark { width: 22px; height: 22px; background: var(--purple); }
  .brand-name {
    font-family: "Roboto Condensed", "Arial Narrow", sans-serif;
    font-weight: 700;
    font-size: 34px;
    color: var(--purple);
    letter-spacing: 0.3px;
  }
  .brand-tagline {
    margin-top: 6px;
    margin-left: 34px;
    font-size: 11px;
    font-weight: 500;
    letter-spacing: 3.2px;
    text-transform: uppercase;
    color: var(--sky);
  }
  .person {
    position: absolute;
    left: 48px;
    top: 140px;
  }
  .person-name {
    font-family: "Roboto Condensed", "Arial Narrow", sans-serif;
    font-weight: 700;
    font-size: 22px;
    color: var(--purple);
    text-transform: uppercase;
  }
  .person-title { font-size: 15px; margin-top: 2px; }
  .address { margin-top: 18px; font-size: 15px; line-height: 1.35; font-style: normal; }
  .contacts { list-style: none; margin-top: 18px; font-size: 15px; line-height: 1.5; }
  .contacts li { display: flex; align-items: center; gap: 9px; }
  .contacts svg { width: 13px; height: 13px; flex: none; }
  .accent-bands {
    position: absolute;
    right: 0;
    bottom: 0;
    width: 280px;
  }
  .accent-bands span { display: block; height: 14px; }
  .band-orange { background: var(--orange); }
  .band-sky { background: var(--sky); }

  /* Back */
  .card-back { background: var(--purple); }
  .back-pattern {
    position: absolute;
    inset: 0;
    background: linear-gradient(135deg, var(--purple-deep), var(--purple) 55%, #9056b2);
  }
  .back-brand {
    position: absolute;
    right: 40px;
    bottom: 36px;
    display: flex;
    align-items: center;
    gap: 10px;
  }
  .back-brand .brand-mark { background: var(--paper); width: 16px; height: 16px; }
  .back-brand .brand-name { color: var(--paper); font-size: 22px; }
</style>
</head>
<body>
  <section class="card card-front" aria-label="Business card front">
    <header class="brand">
      <div class="brand-row">
        <span class="brand-mark"></span>
        <span class="brand-name">Harbor Crest Behavioral Health</span>
      </div>
      <p class="brand-tagline">Dedicated to hope, healing and recovery</p>
    </header>

    <div class="person">
      <h1 class="person-name">Daniel Reyes</h1>
      <p class="person-title">President</p>
      <address class="address">1820 Seabright Lane<br>Cove City CA 90210</address>
      <ul class="contacts">
        <li>
          <svg viewBox="0 0 16 16" aria-hidden="true"><path fill="#00aeef" d="M3.5 1.5l2.5 0 1 3.5-1.6 1.2a8 8 0 0 0 4.4 4.4L11 9l3.5 1v2.5c0 1-1 2-2 2A11 11 0 0 1 1.5 3.5c0-1 1-2 2-2z"/></svg>
          555-310-4827
        </li>
        <li>
          <svg viewBox="0 0 16 16" aria-hidden="true"><rect x="1" y="3" width="14" height="10" rx="1" fill="#f7941d"/><path d="M1.5 3.5L8 9l6.5-5.5" fill="none" stroke="#fff" stroke-width="1.3"/></svg>
          hello@harborcrestbh.com
        </li>
        <li>
          <svg viewBox="0 0 16 16" aria-hidden="true"><circle cx="8" cy="8" r="7" fill="#8dc63f"/><path d="M1 8h14M8 1c3 3 3 11 0 14M8 1c-3 3-3 11 0 14" fill="none" stroke="#fff" stroke-width="1"/></svg>
          www.harborcrestbh.com
        </li>
      </ul>
    </div>

    <div class="accent-bands" aria-hidden="true">
      <span class="band-orange"></span>
      <span class="band-sky"></span>
    </div>
  </section>

  <section class="card card-back" aria-label="Business card back">
    <div class="back-pattern" role="img" aria-label="Repeating brand pattern in tones of purple"></div>
    <div class="back-brand">
      <span class="brand-mark"></span>
      <span class="brand-name">Harbor Crest Behavioral Health</span>
    </div>
  </section>
</body>
</html>
```